Quillmarsh Property Solutions need a business card design

Hello guys. We would need a business card design asap please.
We are a start up property investment business based in London UK specialised in buying, selling, managing and letting properties and helping distressed property owners.
The name of our Business is Quillmarsh, the logo symbolises the four fundamental elements of the world (earth, air, fire and water) and so it stands for strength, stability, longevity.
We would like the business card to communicate professionalism and reliability. Many many thanks indeed for your work.

Details:

1.) Rosalind Updike
Property Investor
Mobile: +44(0)7700123456
Email: rosalind.quillmarsh@mailbox-example.com

2.) Dominic Updike
Property Investor
Mobile: +44(0)7700987654
Email: dominic.quillmarsh@mailbox-example.com

```html
<!DOCTYPE html>
<html lang="en">
<head>
<meta charset="utf-8">
<title>Quillmarsh Property Solutions – Business Card</title>
<link rel="stylesheet" href="https://fonts.googleapis.com/css2?family=Open+Sans:wght@400;600;700;800&display=swap">
<style>
  :root {
    --backdrop: #e9e6e1;
    --card-white: #ffffff;
    --ink: #111111;
    --muted: #555555;
    --brand-blue: #2f63d6;
    --brand-blue-light: #5a8be8;
    --brand-green: #1faa4a;
    --brand-green-deep: #179a3f;
    --line-green: #19a04a;
    --on-dark: #ffffff;
  }
  * { margin: 0; padding: 0; box-sizing: border-box; }
  html, body {
    width: 1200px; height: 720px; overflow: hidden;
    background: var(--backdrop);
    font-family: "Open Sans", Arial, sans-serif;
  }
  .stage {
    position: relative; width: 1200px; height: 720px;
    display: flex; align-items: center; justify-content: center; gap: 40px;
  }
  .card {
    position: relative; width: 540px; height: 308px;
    overflow: hidden; border-radius: 3px;
    box-shadow: 0 6px 18px rgba(0,0,0,0.18);
  }

  /* Front */
  .card-front { background: var(--card-white); }
  .front-band { position: absolute; inset: 0; width: 100%; height: 100%; }
  .holder {
    position: absolute; top: 22px; right: 150px; text-align: left;
  }
  .holder-name {
    color: var(--brand-blue); font-size: 16px; font-weight: 600; line-height: 1.2;
    white-space: nowrap;
  }
  .holder-role {
    color: var(--muted); font-size: 11px; font-weight: 400; margin-top: 2px;
  }
  .brand-lockup {
    position: absolute; left: 44px; top: 120px;
    display: flex; align-items: center; gap: 14px;
  }
  .brand-square {
    width: 46px; height: 46px; background: var(--brand-green);
  }
  .brand-name {
    color: var(--ink); font-weight: 800; text-transform: uppercase;
    font-size: 24px; letter-spacing: 1px; line-height: 1.05;
  }
  .brand-name .sub { display: block; font-size: 11px; letter-spacing: 1.5px; margin-top: 4px; }
  .contacts {
    position: absolute; right: 18px; bottom: 18px;
    list-style: none; color: var(--on-dark); font-size: 10px;
  }
  .contacts li {
    display: flex; align-items: center; justify-content: flex-end; gap: 6px;
    margin-top: 8px; white-space: nowrap;
  }
  .contacts svg { width: 11px; height: 11px; flex: none; }

  /* Back */
  .card-back {
    background: radial-gradient(ellipse at 50% 40%, var(--brand-green) 0%, var(--brand-green-deep) 100%);
    display: flex; flex-direction: column; align-items: center; justify-content: center;
  }
  .back-brand {
    display: flex; align-items: center; gap: 14px; margin-top: -10px;
  }
  .back-circle { width: 54px; height: 54px; border-radius: 50%; background: var(--on-dark); }
  .back-brand .brand-name { color: var(--on-dark); font-size: 34px; }
  .website {
    color: var(--on-dark); font-size: 17px; letter-spacing: 1.5px; margin-top: 48px;
  }
</style>
</head>
<body>
<main class="stage">

  <section class="card card-front" aria-label="Business card front">
    <svg class="front-band" viewBox="0 0 540 308" preserveAspectRatio="none" aria-hidden="true">
      <defs>
        <linearGradient id="bandBlue" x1="0" y1="1" x2="1" y2="0">
          <stop offset="0" stop-color="#5a8be8"/>
          <stop offset="1" stop-color="#2f63d6"/>
        </linearGradient>
      </defs>
      <line x1="430" y1="0" x2="250" y2="308" stroke="#19a04a" stroke-width="3"/>
      <polygon points="441,0 540,0 540,308 262,308" fill="url(#bandBlue)"/>
    </svg>

    <div class="holder">
      <p class="holder-name">Rosalind Updike</p>
      <p class="holder-role">Property Investor</p>
    </div>

    <div class="brand-lockup">
      <span class="brand-square" aria-hidden="true"></span>
      <p class="brand-name">Quillmarsh<span class="sub">Property Solutions</span></p>
    </div>

    <ul class="contacts">
      <li>
        <svg viewBox="0 0 12 12" aria-hidden="true"><rect x="3" y="0.5" width="6" height="11" rx="1.2" fill="none" stroke="currentColor" stroke-width="1.2"/><circle cx="6" cy="9.5" r="0.8" fill="currentColor"/></svg>
        +44(0)7700123456
      </li>
      <li>
        <svg viewBox="0 0 12 12" aria-hidden="true"><rect x="0.8" y="2.5" width="10.4" height="7" rx="1" fill="none" stroke="currentColor" stroke-width="1.2"/><path d="M1 3 L6 7 L11 3" fill="none" stroke="currentColor" stroke-width="1.2"/></svg>
        rosalind.quillmarsh@mailbox-example.com
      </li>
    </ul>
  </section>

  <section class="card card-back" aria-label="Business card back">
    <div class="back-brand">
      <span class="back-circle" aria-hidden="true"></span>
      <p class="brand-name">Quillmarsh</p>
    </div>
    <p class="website">www.quillmarsh-example.com</p>
  </section>

</main>
</body>
</html>
```